Classy, Elegant, Simple Business Card Design

Looking to have a classy, simple, and elegant design. Want a top notch designed business card. I really like the look of the new torvane credit card. I also like the design I attached. I am trying to reach 21-29 year old females for booking us for there wedding or event. We offer Disc Jockey Service, Photo Booth Rentals, and Uplighting .

Target Market(s)

21-28 year old females

Contact Information for Business Card

Has to have logo, website, email, and phone number

Font styles to use
Other font styles liked:
• open to font choice, modern, clean
Designer to choose
33a6d7
0791cd
0555a3
ffffff

Requirements
Must have
• Has to have logo, website, email, and phone number
Nice to have
• I really like the design of the new torvane credit card. I also included my logo and some designs I like
Should not have
• clutter or too much info

```html
<!DOCTYPE html>
<html lang="en">
<head>
<meta charset="utf-8">
<title>Tidewell Events – Business Card</title>
<link rel="stylesheet" href="https://fonts.googleapis.com/css2?family=Lato:wght@400;700&display=swap">
<style>
  :root {
    --navy: #14325c;
    --blue: #0791cd;
    --blue-deep: #0555a3;
    --sky: #33a6d7;
    --white: #ffffff;
    --paper: #f4f4f4;
    --stage: #e6e8ec;
  }
  * { margin: 0; padding: 0; box-sizing: border-box; }
  html, body {
    width: 1200px; height: 1015px; overflow: hidden;
    background: var(--stage);
    font-family: 'Lato', sans-serif;
  }
  .sheet {
    position: relative; width: 1200px; height: 1015px;
    display: flex; flex-direction: column; align-items: center;
    gap: 25px; padding-top: 15px;
  }
  .card {
    position: relative; width: 840px; height: 480px; overflow: hidden;
    box-shadow: 0 8px 22px rgba(0,0,0,.18);
  }
  .card-back {
    background: var(--navy);
    display: flex; align-items: center; justify-content: center;
  }
  .wordmark {
    display: flex; align-items: center; gap: 14px;
    color: var(--blue); font-weight: 700; letter-spacing: 1px;
    white-space: nowrap;
  }
  .wordmark .dot {
    width: 22px; height: 22px; border-radius: 50%; background: var(--blue);
    flex: none;
  }
  .card-back .wordmark { font-size: 58px; color: var(--sky); gap: 18px; }
  .card-back .wordmark .dot { width: 26px; height: 26px; background: var(--sky); }

  .card-front { background: var(--paper); }
  .card-front .shape { position: absolute; inset: 0; }
  .card-front .wordmark {
    position: absolute; left: 520px; top: 196px; font-size: 30px;
  }
  .contacts {
    position: absolute; left: 62px; top: 160px;
    list-style: none; color: var(--white); font-size: 20px;
  }
  .contacts li { display: flex; align-items: center; gap: 12px; margin-bottom: 8px; }
  .contacts .icon {
    width: 22px; height: 22px; border-radius: 50%; background: var(--blue);
    display: flex; align-items: center; justify-content: center; flex: none;
  }
  .services {
    position: absolute; left: 100px; top: 320px;
    list-style: none; color: var(--white); font-size: 21px; line-height: 1.3;
  }
  .services li { display: flex; align-items: center; gap: 12px; }
  .services li::before {
    content: ""; width: 9px; height: 9px; border-radius: 50%; background: var(--blue);
  }
</style>
</head>
<body>
<main class="sheet">
  <section class="card card-back" aria-label="Card back">
    <div class="wordmark"><span class="dot"></span><span>Tidewell Events</span></div>
  </section>

  <section class="card card-front" aria-label="Card front">
    <svg class="shape" viewBox="0 0 840 480" width="840" height="480" aria-hidden="true">
      <circle cx="230" cy="240" r="252" fill="var(--blue)"/>
      <circle cx="223" cy="240" r="247" fill="var(--paper)"/>
      <circle cx="218" cy="240" r="242" fill="var(--navy)"/>
    </svg>

    <ul class="contacts">
      <li><span class="icon">
        <svg width="12" height="12" viewBox="0 0 12 12"><path d="M2 1 L4.5 1 L5.2 3.6 L3.8 4.6 Q5 7.2 7.4 8.3 L8.4 6.9 L11 7.6 L11 10 Q6 11 2 6 Q1 3.5 2 1 Z" fill="#fff"/></svg>
      </span>044-555 010 789</li>
      <li><span class="icon">
        <svg width="12" height="10" viewBox="0 0 12 10"><rect x="0.5" y="0.5" width="11" height="9" fill="none" stroke="#fff"/><path d="M0.5 0.5 L6 5.5 L11.5 0.5" fill="none" stroke="#fff"/></svg>
      </span>hello@tidewellevents.com</li>
      <li><span class="icon">
        <svg width="12" height="12" viewBox="0 0 12 12"><circle cx="6" cy="6" r="5" fill="none" stroke="#fff"/><path d="M1 6 H11 M6 1 Q3 6 6 11 Q9 6 6 1" fill="none" stroke="#fff"/></svg>
      </span>www.tidewellevents.com</li>
    </ul>

    <ul class="services">
      <li>Disc Jockey Service</li>
      <li>Photo Booth Rentals</li>
      <li>Uplighting</li>
    </ul>

    <div class="wordmark"><span class="dot"></span><span>Tidewell Events</span></div>
  </section>
</main>
</body>
</html>
```